Retractable banner.
Health Check For Pets
Check for Ear Mites
Skin Health
Fleas & Ticks

A space SERVE BY <NAME OF CLINIC>

Ideally contain pictures of cats and dogs

```html
<!DOCTYPE html>
<html lang="en">
<head>
<meta charset="utf-8">
<title>Health Check For Pets – Retractable Banner</title>
<link href="https://fonts.googleapis.com/css2?family=Roboto+Slab:wght@800;900&family=Montserrat:wght@800;900&display=swap" rel="stylesheet">
<style>
  :root {
    --banner-white: #fbfaf6;
    --brand-green: #2f8f2f;
    --brand-red: #c8102e;
    --ink: #1d1d1b;
    --photo-light: #e9ece8;
    --photo-mid: #c9cfc7;
    --photo-dark: #55606a;
  }
  html, body {
    margin: 0;
    padding: 0;
    width: 1200px;
    height: 825px;
    overflow: hidden;
    background: var(--banner-white);
  }
  .banner {
    position: relative;
    width: 1200px;
    height: 825px;
    overflow: hidden;
    background: var(--banner-white);
  }
  .banner-graphics {
    position: absolute;
    inset: 0;
  }
  .headline {
    position: absolute;
    left: 58px;
    top: 70px;
    margin: 0;
    font-family: "Roboto Slab", serif;
    font-weight: 900;
    line-height: 0.95;
    text-transform: uppercase;
  }
  .headline-top {
    display: block;
    color: var(--brand-green);
    font-size: 78px;
    letter-spacing: 1px;
  }
  .headline-main {
    display: block;
    color: var(--brand-red);
    font-size: 138px;
    letter-spacing: 2px;
  }
  .checks {
    position: absolute;
    left: 0;
    top: 390px;
    width: 640px;
    height: 170px;
    display: flex;
    align-items: center;
    padding-left: 40px;
    box-sizing: border-box;
  }
  .check-item {
    flex: 0 0 auto;
    padding: 0 26px;
    color: var(--banner-white);
    font-family: "Montserrat", sans-serif;
    font-weight: 900;
    font-size: 42px;
    line-height: 1.08;
    text-align: center;
    text-transform: uppercase;
  }
  .check-item + .check-item {
    border-left: 4px solid var(--banner-white);
  }
  .served-by {
    position: absolute;
    left: 40px;
    top: 596px;
    width: 560px;
    display: flex;
    align-items: center;
    gap: 14px;
    color: var(--brand-green);
    font-family: "Montserrat", sans-serif;
    font-weight: 800;
    font-size: 26px;
    letter-spacing: 1px;
    text-transform: uppercase;
  }
  .served-by::before,
  .served-by::after {
    content: "";
    flex: 1;
    height: 3px;
    background: var(--brand-green);
  }
  .clinic-name {
    position: absolute;
    left: 40px;
    top: 648px;
    width: 600px;
    margin: 0;
    color: var(--brand-red);
    font-family: "Montserrat", sans-serif;
    font-weight: 900;
    font-size: 54px;
    text-align: center;
  }
</style>
</head>
<body>
<main class="banner">
  <svg class="banner-graphics" width="1200" height="825" viewBox="0 0 1200 825" aria-hidden="false">
    <defs>
      <linearGradient id="photo-tone" x1="0" y1="0" x2="1" y2="1">
        <stop offset="0" stop-color="var(--photo-light)"/>
        <stop offset="0.55" stop-color="var(--photo-mid)"/>
        <stop offset="1" stop-color="var(--photo-dark)"/>
      </linearGradient>
    </defs>

    <!-- green checklist band -->
    <rect class="checks-band" x="0" y="380" width="760" height="190" fill="var(--brand-green)"/>
    <polygon points="92,380 132,380 112,402" fill="var(--banner-white)"/>
    <polygon points="292,380 332,380 312,402" fill="var(--banner-white)"/>
    <polygon points="486,380 526,380 506,402" fill="var(--banner-white)"/>

    <!-- photo area -->
    <path class="photo-area" d="M1200 40 Q700 220 660 825 L1200 825 Z" fill="url(#photo-tone)"
          role="img" aria-label="Photo of a veterinarian examining a small dog's coat with a penlight"/>
    <path class="photo-edge" d="M1200 40 Q700 220 660 825" fill="none" stroke="var(--brand-green)" stroke-width="14"/>

    <!-- topic badges -->
    <g class="topic-badge">
      <circle cx="1018" cy="129" r="66" fill="var(--banner-white)" stroke="var(--ink)" stroke-width="5"/>
      <circle cx="1018" cy="129" r="38" fill="#e6d27a" role="img" aria-label="Illustration of an ear mite"/>
    </g>
    <g class="topic-badge">
      <circle cx="874" cy="252" r="66" fill="var(--banner-white)" stroke="var(--ink)" stroke-width="5"/>
      <circle cx="874" cy="252" r="38" fill="#8fb3e6" role="img" aria-label="Illustration of a dog scratching its skin"/>
    </g>
    <g class="topic-badge">
      <circle cx="766" cy="409" r="66" fill="var(--banner-white)" stroke="var(--ink)" stroke-width="5"/>
      <circle cx="766" cy="409" r="38" fill="#8a4a22" role="img" aria-label="Illustration of a tick"/>
    </g>
  </svg>

  <h1 class="headline">
    <span class="headline-top">Health Check</span>
    <span class="headline-main">For Pets</span>
  </h1>

  <ul class="checks" style="list-style:none;margin:0;">
    <li class="check-item">Ear<br>Mites</li>
    <li class="check-item">Skin<br>Health</li>
    <li class="check-item">Fleas<br>&amp; Ticks</li>
  </ul>

  <p class="served-by" style="margin:0;">Serve by:</p>
  <p class="clinic-name">Pet Health Care CLINIC</p>
</main>
</body>
</html>
```